Business card design needed

Family General Practitioner/ Family Physician.
Logo is the logo of the Noble Guild of Family Healers Oceania
http://kpltw.varendo.example/ImageShelf/marks/pages/NGFHO%20mark_jpg.htm
Updates

Project Deadline Extended
Reason: Just a bit more time to make changes and the weekend for me to look at things closely and to choose. Thanks, Orin

Thanks for all the submissions. So many of them are really works of art. Not one of them are not good. The ones that I am eliminating are the ones that I think are not suitable for me personally only, and because if I don't, it makes it very difficult to decide as many of you are also sending me slight variations of a card. I have just decided to choose a second place card too. Can't thank you all enough. Good luck, Orin. P.S - Working today till 10 pm as the card says :-), so probably won't be able to give a feedback till late Saturday night or Sunday morning here in Sydney, Australia. 

Project Deadline Extended
Reason: Just added a second place to the budget and realised that Australia is ahead of the rest of the world in the time zone (only :-) - don't want to offend anyone or start a debate!! ) , so Monday deadline will mean it will be a weekend for the rest of the world. Just wanted to give everyone more time to submit their best, especially since I will be picking a second card too. Can't thank everyone enough for the submissions. P.S - Not keen on photos on the card.

Industry/Entity Type

Business

Contact Information for Business Card

Dr. Orin Halvey M.B.B.S., F.N.G.F.H.O
Family General Practitioner
Address, timings, phone and fax number on the back.

Requirements
Must have
• Timings
Mon 7 am - 7 pm
Tues 7 am - 12 pm
Wed 7 am - 10 pm
Thurs 7 am - 12 pm
Fri 7 am - 8 pm
Sat 8 am - 10 pm
Sun - Off

```html
<!DOCTYPE html>
<html lang="en">
<head>
<meta charset="utf-8">
<title>Dr. Orin Halvey – Business Card</title>
<link rel="stylesheet" href="https://fonts.googleapis.com/css2?family=Lato:wght@400;700;900&display=swap">
<style>
  :root {
    --bg: #2b2b2b;
    --card-white: #ffffff;
    --card-fade: #ececec;
    --yellow: #f3d23c;
    --ink: #161616;
    --row-1-day: #3a3a3a; --row-1-time: #0f0f0f;
    --row-2-day: #454441; --row-2-time: #171716;
    --row-3-day: #55524a; --row-3-time: #26251f;
    --row-4-day: #645f50; --row-4-time: #37342a;
    --row-5-day: #736c55; --row-5-time: #474230;
    --row-6-day: #807759; --row-6-time: #524b33;
    --row-7-day: #8a805d; --row-7-time: #5d5435;
    --cell-text: #ffffff;
  }
  * { box-sizing: border-box; margin: 0; padding: 0; }
  html, body { width: 1200px; height: 746px; overflow: hidden; }
  body {
    background: var(--bg);
    font-family: "Lato", Arial, sans-serif;
    color: var(--ink);
    position: relative;
  }

  /* Front */
  .card-front {
    position: absolute; left: 62px; top: 56px; width: 498px; height: 319px;
    background: radial-gradient(ellipse at 45% 40%, var(--card-white) 40%, var(--card-fade) 100%);
    overflow: hidden;
  }
  .guild-name {
    position: absolute; right: 18px; top: 14px; width: 92px;
    font-size: 9px; font-weight: 700; line-height: 1.25; text-align: center;
    color: var(--ink);
  }
  .family-illustration {
    position: absolute; left: 104px; top: 90px; width: 290px; height: 100px;
    background: linear-gradient(90deg, var(--yellow), #f7e382 50%, var(--yellow));
    border-radius: 4px;
  }
  .identity {
    position: absolute; left: 0; right: 0; top: 205px; text-align: center;
  }
  .doctor-name { font-size: 23px; font-weight: 400; letter-spacing: 0.3px; line-height: 1.1; }
  .doctor-name strong { font-weight: 900; }
  .credentials { font-size: 13px; font-weight: 400; line-height: 1.4; }
  .specialty { font-size: 19px; font-weight: 400; line-height: 1.2; }
  .specialty strong { font-weight: 900; }
  .front-band {
    position: absolute; left: 0; right: 0; bottom: 0; height: 32px; background: var(--yellow);
  }

  /* Back */
  .card-back {
    position: absolute; left: 616px; top: 336px; width: 498px; height: 320px;
    background: var(--yellow);
  }
  .contact {
    position: absolute; left: 30px; top: 54px; width: 210px;
    font-size: 13.5px; line-height: 18px;
  }
  .contact-label { font-weight: 900; font-size: 13.5px; }
  .contact-value { padding-left: 16px; white-space: nowrap; }
  .contact-group + .contact-group { margin-top: 18px; }
  .contact-group.phone .contact-value,
  .contact-group.fax .contact-value { padding-left: 13px; }

  .hours {
    position: absolute; left: 248px; top: 41px; width: 250px;
    border-collapse: separate; border-spacing: 0 7px;
    font-size: 13.5px; color: var(--cell-text);
  }
  .hours td { height: 26px; padding: 0 8px; white-space: nowrap; }
  .hours .day { width: 100px; font-weight: 700; }
  .hours .time { font-weight: 400; }
  .hours tr:nth-child(1) .day { background: var(--row-1-day); } .hours tr:nth-child(1) .time { background: var(--row-1-time); }
  .hours tr:nth-child(2) .day { background: var(--row-2-day); } .hours tr:nth-child(2) .time { background: var(--row-2-time); }
  .hours tr:nth-child(3) .day { background: var(--row-3-day); } .hours tr:nth-child(3) .time { background: var(--row-3-time); }
  .hours tr:nth-child(4) .day { background: var(--row-4-day); } .hours tr:nth-child(4) .time { background: var(--row-4-time); }
  .hours tr:nth-child(5) .day { background: var(--row-5-day); } .hours tr:nth-child(5) .time { background: var(--row-5-time); }
  .hours tr:nth-child(6) .day { background: var(--row-6-day); } .hours tr:nth-child(6) .time { background: var(--row-6-time); }
  .hours tr:nth-child(7) .day { background: var(--row-7-day); } .hours tr:nth-child(7) .time { background: var(--row-7-time); }
</style>
</head>
<body>

<section class="card-front">
  <div class="guild-name">Noble Guild of Family Healers Oceania</div>
  <div class="family-illustration" role="img" aria-label="Stick-figure family in black and yellow: an elder with a cane, adults and two children walking together"></div>
  <div class="identity">
    <p class="doctor-name">DR. ORIN <strong>HALVEY</strong></p>
    <p class="credentials">M. B. B. S. , F.N.G.F.H.O</p>
    <p class="specialty">FAMILY <strong>GENERAL PRACTITIONER</strong></p>
  </div>
  <div class="front-band"></div>
</section>

<section class="card-back">
  <div class="contact">
    <div class="contact-group address">
      <p class="contact-label">ADDRESS:</p>
      <p class="contact-value">Upper Level,<br>Merrow Court,<br>Wrenfield Shopping Centre<br>Harlow Ridge,<br>NSW&nbsp; 2199</p>
    </div>
    <div class="contact-group phone">
      <p class="contact-label">PHONE:</p>
      <p class="contact-value">02 5550 1840</p>
    </div>
    <div class="contact-group fax">
      <p class="contact-label">FAX:</p>
      <p class="contact-value">02 5550 1872</p>
    </div>
  </div>

  <table class="hours">
    <tr><td class="day">MONDAY</td><td class="time">07:00 AM - 07:00 PM</td></tr>
    <tr><td class="day">TUESDAY</td><td class="time">07:00 AM - 12:00 PM</td></tr>
    <tr><td class="day">WEDNESDAY</td><td class="time">07:00 AM - 10:00 PM</td></tr>
    <tr><td class="day">THURSDAY</td><td class="time">07:00 AM - 12:00 PM</td></tr>
    <tr><td class="day">FRIDAY</td><td class="time">07:00 AM - 08:00 PM</td></tr>
    <tr><td class="day">SATURDAY</td><td class="time">08:00 AM - 10:00 PM</td></tr>
    <tr><td class="day">SUNDAY</td><td class="time">OFF</td></tr>
  </table>
</section>

</body>
</html>
```